Business cards for a fun web development agency

Hi,I am building a web development agency. You can read about it on the website http://kite-loft.examplehost.com. Basically, I want to focus on free and open source products and stay as far away from the corporate business feeling as possible. I want to build a community so I want the business card to feel fun and approachable (at the risk of professional if need be). I am uploading some of my image assets in various file formats. Feel free to use them or make your own if you want just keeping in theme with the website.
Industry/Entity Type
Building
Contact Information for Business Card
Company Name: Boat ShedWebsite: www.kiteloftdev.example (it's currently in alpha on http://kite-loft.examplehost.com if you want to see the them we are trying to capture)My name is: Banner B. SchaferMy email: banner@boatsheddev.comMy phone: 0431 587 904
Look and feel

```html
<!DOCTYPE html>
<html lang="en">
<head>
<meta charset="utf-8">
<title>Kite Loft Business Cards</title>
<link href="https://fonts.googleapis.com/css2?family=Open+Sans:wght@400;700&family=Montserrat:wght@400&display=swap" rel="stylesheet">
<style>
  :root {
    --backdrop: #3b3b3d;
    --card: #ffffff;
    --navy: #1d4a86;
    --blue: #1a6fc4;
    --blue-light: #4b98dc;
    --water-top: #9ed6de;
    --water-bottom: #62b3c4;
    --ink: #2a3f5f;
  }
  * { margin: 0; padding: 0; box-sizing: border-box; }
  html, body {
    width: 1200px; height: 852px; overflow: hidden;
    background: var(--backdrop);
    font-family: "Open Sans", Arial, sans-serif;
  }
  .stage { position: relative; width: 1200px; height: 852px; }
  .card {
    position: absolute;
    width: 500px; height: 290px;
    background: var(--card);
    border-radius: 22px;
    overflow: hidden;
    box-shadow: 0 14px 30px rgba(0,0,0,0.45);
  }
  .card--front { left: 90px; top: 130px; display: flex; align-items: center; justify-content: center; }
  .card--back { left: 610px; top: 432px; }

  .wordmark {
    display: flex; align-items: center; gap: 12px;
    font-family: "Montserrat", Arial, sans-serif;
    font-weight: 400; color: var(--navy);
    letter-spacing: 1px; white-space: nowrap;
  }
  .wordmark__dot { border-radius: 50%; background: var(--blue); flex: none; }
  .card--front .wordmark { font-size: 50px; }
  .card--front .wordmark__dot { width: 40px; height: 40px; }

  .card--back .wordmark { position: absolute; left: 34px; top: 112px; font-size: 36px; }
  .card--back .wordmark__dot { width: 30px; height: 30px; }

  .backdrop-art { position: absolute; inset: 0; width: 500px; height: 290px; }

  .holder { position: absolute; right: 30px; top: 26px; text-align: right; color: var(--ink); }
  .holder__name { font-weight: 700; font-size: 15px; }
  .holder__title { font-size: 11px; margin-top: 2px; }

  .contacts { position: absolute; left: 36px; top: 178px; list-style: none; color: var(--ink); font-size: 13px; }
  .contacts li { display: flex; align-items: center; gap: 10px; line-height: 21px; }
  .contacts svg { width: 11px; height: 11px; fill: var(--ink); flex: none; }
</style>
</head>
<body>
<main class="stage">
  <section class="card card--front" aria-label="Card front">
    <div class="wordmark"><span>KITE</span><span class="wordmark__dot"></span><span>LOFT</span></div>
  </section>

  <section class="card card--back" aria-label="Card back">
    <svg class="backdrop-art" viewBox="0 0 500 290" aria-hidden="false">
      <defs>
        <linearGradient id="water" x1="0" y1="0" x2="0" y2="1">
          <stop offset="0" stop-color="var(--water-top)"/>
          <stop offset="1" stop-color="var(--water-bottom)"/>
        </linearGradient>
      </defs>
      <path role="img" aria-label="Illustration of a blue house on stilts over the water with a school of fish"
            fill="url(#water)"
            d="M500 58 C430 66 395 150 330 205 C270 250 140 262 0 262 L0 290 L500 290 Z"/>
      <path fill="none" stroke="var(--blue)" stroke-width="9"
            d="M500 48 C420 58 385 150 320 200 C260 245 140 255 0 252"/>
      <path fill="none" stroke="var(--blue-light)" stroke-width="3"
            d="M470 62 C410 80 380 165 315 212 C255 255 140 264 20 262"/>
    </svg>

    <div class="holder">
      <div class="holder__name">Corwin T. Aldous</div>
      <div class="holder__title">Managing Director</div>
    </div>

    <div class="wordmark"><span>KITE</span><span class="wordmark__dot"></span><span>LOFT</span></div>

    <ul class="contacts">
      <li><svg viewBox="0 0 12 12"><path d="M2 1h2.5l1 3-1.5 1c.6 1.3 1.7 2.4 3 3l1-1.5 3 1V10c0 .6-.4 1-1 1C5 11 1 7 1 2c0-.6.4-1 1-1z"/></svg>0431 587 904</li>
      <li><svg viewBox="0 0 12 12"><path d="M1 2.5h10v7H1z M1 2.5l5 4 5-4" stroke="#fff" stroke-width="0.8"/></svg>corwin@kiteloftdev.example</li>
      <li><svg viewBox="0 0 12 12"><circle cx="6" cy="6" r="5"/></svg>www.kiteloftdev.example</li>
    </ul>
  </section>
</main>
</body>
</html>
```